Business Card for beauty technology startup

Design Glimora Business Card for a Beauty, based on the website identity and colors (https://www.glimora-example.com).
Glimora is a beauty tech startup that gathers helpful product info for beauty lovers and consumers (such as availability on stores, price range and product reviews) for makeup products. The card design must be young, colorful but clean, and very modern.

Target Market(s)

woman, 15-35

Industry/Entity Type

Cosmetics

Contact Information for Business Card

Full Name, address, phone

Font styles to use
Other font styles liked:
• Advent Pro

Colors
e34297
86cfc6
ffffff
5c5c5c
e8e8e8
e667a6
b2b2b2

Requirements
Must have
• One full colored side with a creative design and another with card info
• Use Color palette: #95C5C5 and/or #D38AA5
• Use fonts: Advent Pro
• Use website identity: https://www.glimora-example.com
Nice to have
• If needed extra font: Roboto

```html
<!DOCTYPE html>
<html lang="en">
<head>
<meta charset="utf-8">
<title>Glimora Business Card</title>
<link rel="stylesheet" href="https://fonts.googleapis.com/css2?family=Josefin+Sans:wght@300&family=Roboto:wght@400;500&family=Roboto+Condensed:wght@500&display=swap">
<style>
  :root {
    --backdrop: #e6e3df;
    --card-dark: #17171a;
    --card-light: #fbfbfb;
    --brand-rose: #b87b91;
    --faint-rose: #efe5e9;
    --text-light: #f2f2f2;
    --text-muted: #b2b2b2;
    --text-grey: #5c5c5c;
  }
  * { margin: 0; padding: 0; box-sizing: border-box; }
  html, body { width: 1200px; height: 960px; overflow: hidden; }
  body {
    position: relative;
    background: var(--backdrop);
    font-family: "Roboto", Arial, sans-serif;
  }
  .card {
    position: absolute;
    width: 600px;
    height: 342px;
    border-radius: 18px;
    overflow: hidden;
    box-shadow: 0 3px 8px rgba(0,0,0,0.25);
  }
  .card--front { left: 315px; top: 113px; background: var(--card-dark); }
  .card--back { left: 311px; top: 471px; background: var(--card-light); }

  .front-accent { position: absolute; inset: 0; }

  .brand-mark {
    position: absolute;
    left: 25px;
    top: 35px;
    display: flex;
    align-items: center;
    gap: 12px;
  }
  .brand-mark__dot {
    width: 32px; height: 32px;
    border: 2px solid var(--brand-rose);
    border-radius: 50%;
  }
  .brand-mark__name {
    font-family: "Josefin Sans", Arial, sans-serif;
    font-weight: 300;
    font-size: 34px;
    letter-spacing: 4px;
    color: var(--brand-rose);
    line-height: 1;
    padding-top: 6px;
  }

  .contact { position: absolute; left: 28px; top: 133px; }
  .contact__name {
    font-family: "Roboto Condensed", Arial, sans-serif;
    font-weight: 500;
    font-size: 20px;
    color: var(--brand-rose);
  }
  .contact__title {
    font-size: 14px;
    color: var(--text-muted);
    margin-top: 2px;
  }
  .contact__address {
    margin-top: 15px;
    font-size: 14px;
    line-height: 18px;
    color: var(--text-light);
  }
  .contact__lines { margin-top: 11px; list-style: none; }
  .contact__lines li {
    display: flex;
    align-items: center;
    gap: 8px;
    font-size: 14px;
    line-height: 19px;
    color: var(--text-light);
  }
  .contact__lines svg { width: 13px; height: 13px; fill: var(--brand-rose); }

  .back-ring { position: absolute; inset: 0; }
  .back-brand {
    position: absolute;
    right: 33px;
    bottom: 26px;
    text-align: right;
  }
  .back-brand__name {
    font-family: "Josefin Sans", Arial, sans-serif;
    font-weight: 300;
    font-size: 50px;
    letter-spacing: 5px;
    color: var(--brand-rose);
    line-height: 1;
  }
  .back-brand__url {
    margin-top: 6px;
    font-size: 13px;
    letter-spacing: 3px;
    color: var(--text-grey);
  }
</style>
</head>
<body>
  <section class="card card--front">
    <svg class="front-accent" width="600" height="342" viewBox="0 0 600 342" aria-hidden="true">
      <rect x="430" y="0" width="170" height="342" fill="var(--brand-rose)"/>
      <circle cx="430" cy="170" r="172" fill="var(--brand-rose)"/>
    </svg>

    <div class="brand-mark">
      <span class="brand-mark__dot"></span>
      <span class="brand-mark__name">GLIMORA</span>
    </div>

    <div class="contact">
      <h1 class="contact__name">CLARA WENDT</h1>
      <p class="contact__title">CEO/FOUNDER</p>
      <p class="contact__address">2140 Larkspur Court<br>Juneau, Alaska 34910</p>
      <ul class="contact__lines">
        <li><svg viewBox="0 0 24 24"><path d="M6.6 10.8a15.1 15.1 0 0 0 6.6 6.6l2.2-2.2c.3-.3.7-.4 1-.2 1.1.4 2.3.6 3.6.6.6 0 1 .4 1 1V20c0 .6-.4 1-1 1A17 17 0 0 1 3 4c0-.6.4-1 1-1h3.5c.6 0 1 .4 1 1 0 1.3.2 2.5.6 3.6.1.3 0 .7-.2 1z"/></svg>555 014 2871</li>
        <li><svg viewBox="0 0 24 24"><path d="M7 1h10a2 2 0 0 1 2 2v18a2 2 0 0 1-2 2H7a2 2 0 0 1-2-2V3a2 2 0 0 1 2-2zm0 3v15h10V4zm5 16a1 1 0 1 0 0 2 1 1 0 0 0 0-2z"/></svg>555 019 6403</li>
        <li><svg viewBox="0 0 24 24"><path d="M6 2h12v5H6zM4 8h16a2 2 0 0 1 2 2v7h-4v5H6v-5H2v-7a2 2 0 0 1 2-2zm4 8v4h8v-4z"/></svg>555 012 7759</li>
        <li><svg viewBox="0 0 24 24"><path d="M2 5h20v14H2zm2 2v.5l8 5 8-5V7l-8 5z"/></svg>info@glimora-example.com</li>
      </ul>
    </div>
  </section>

  <section class="card card--back">
    <svg class="back-ring" width="600" height="342" viewBox="0 0 600 342" aria-hidden="true">
      <circle cx="172" cy="170" r="162" fill="none" stroke="var(--faint-rose)" stroke-width="4"/>
    </svg>
    <div class="back-brand">
      <p class="back-brand__name">GLIMORA</p>
      <p class="back-brand__url">www.glimora-example.com</p>
    </div>
  </section>
</body>
</html>
```